Valdane Companies Business Card Design

We need a new business card for our Private Equity Real Estate Development firm, “Valdane” and our EB-5 regional center “Thornmere Regional Center” on one card. We prefer a design that is simple, elegant, and represents the luxury products we design and build as well as the financial security and stability our successful history has produced. We are an industry leader in our field and 3rd generation family business that has evolved into an institutional quality investment platform. Considered design size is standard business card dimensions (3.5 x 2 inches with an additional 1/8 inch space for design elements or backgrounds that extend beyond the finished size of your piece.

Target Market(s)

• High net worth individuals
• Highly skilled technical workers and physicians in the US seeking investment-based immigration opportunities
• Sophisticated private equity investors
• Intermediary partners include domestic attorneys and investment brokers, as well as international agent networks
• US real estate developers

Industry/Entity Type

Finance

Contact Information for Business Card

(Providing placeholder info for personal information, please design for longer character spaces, longer names and addresses etc..)
• Logo for Valdane
• Logo for Thornmere Regional Center
• Full name: Marcus Valdane
• Job title: CEO
• Email address: mvaldane@valdanecompanies.com
• Cell phone number: +1.555.314.2287
• Office number +1.555.628.4410
• Office address: Larkfield Court 5, 4817 Vista Orilla, San Ramon, CA.
• Website: www.valdanecompanies.com

Font styles to use
Serif
Sans Serif

Colors
ec1f27
ffffff
000000

Requirements
Must have
• • Logo for Valdane
• • Logo for Thornmere Regional Center
• - Use rounded corners
• (See .ai file included for logos)
Nice to have
• • Simple, elegant design
• • Aesthetically compatible with our website design (www.valdanecompanies.com)
• • Color palette including but not limited to white, black, and red (as per logos)
Should not have
• - Not too much red color
• - Do not stack both logos on top of each other

```html
<!DOCTYPE html>
<html lang="en">
<head>
<meta charset="utf-8">
<title>Valdane Companies Business Card</title>
<link href="https://fonts.googleapis.com/css2?family=Source+Sans+3:wght@400;600&display=swap" rel="stylesheet">
<style>
  :root {
    --backdrop: #2b2b2b;
    --card: #262626;
    --ink: #ffffff;
    --ink-soft: #e6e6e6;
    --brand-red: #a51d30;
  }
  html, body {
    margin: 0;
    width: 1200px;
    height: 1200px;
    overflow: hidden;
    background: var(--backdrop);
    font-family: "Source Sans 3", "Source Sans Pro", sans-serif;
  }
  .card {
    position: absolute;
    left: 193px;
    width: 880px;
    height: 502px;
    background: var(--card);
    border-radius: 32px;
    box-shadow: 0 18px 40px rgba(0,0,0,0.55);
  }
  .card--front { top: 34px; }
  .card--back { top: 664px; }

  .wordmark {
    position: absolute;
    left: 39px;
    top: 60px;
    display: flex;
    align-items: center;
    gap: 16px;
    color: var(--ink);
    font-weight: 600;
    font-size: 44px;
    letter-spacing: 1px;
  }
  .wordmark__square {
    width: 22px;
    height: 22px;
    background: var(--ink);
  }

  .person { position: absolute; left: 38px; top: 190px; color: var(--ink); }
  .person__name { margin: 0; font-size: 34px; font-weight: 600; line-height: 1.1; }
  .person__title { margin: 6px 0 0 2px; font-size: 20px; font-weight: 400; }

  .address {
    position: absolute;
    left: 39px;
    top: 278px;
    margin: 0;
    font-style: normal;
    font-size: 20px;
    line-height: 21px;
    color: var(--ink-soft);
  }

  .contacts {
    position: absolute;
    left: 39px;
    top: 342px;
    margin: 0;
    padding: 0;
    list-style: none;
    color: var(--ink-soft);
    font-size: 19px;
  }
  .contacts li {
    display: flex;
    align-items: center;
    height: 29px;
  }
  .contacts svg {
    width: 18px;
    height: 18px;
    margin-right: 24px;
    flex: none;
  }

  .regional-mark {
    position: absolute;
    right: 40px;
    top: 390px;
    display: flex;
    align-items: center;
    gap: 14px;
    color: var(--brand-red);
    font-weight: 600;
    font-size: 32px;
  }
  .regional-mark__square {
    width: 18px;
    height: 18px;
    background: var(--brand-red);
  }
</style>
</head>
<body>

<section class="card card--front">
  <div class="wordmark"><span class="wordmark__square"></span>Valdane Capital</div>

  <div class="person">
    <h1 class="person__name">Marcus Valdane</h1>
    <p class="person__title">CEO</p>
  </div>

  <address class="address">
    Larkfield Court 5, 4817<br>
    Vista Orilla San Ramon, CA
  </address>

  <ul class="contacts">
    <li>
      <svg viewBox="0 0 18 18" fill="none" stroke="#fff" stroke-width="1.6"><rect x="4.5" y="1" width="9" height="16" rx="1.5"/><line x1="8" y1="14.5" x2="10" y2="14.5"/></svg>
      +1555 - 314 - 2287
    </li>
    <li>
      <svg viewBox="0 0 18 18" fill="#fff"><path d="M1 6c2-3 14-3 16 0v2h-4V6.5H5V8H1z"/><path d="M4 9h10l2 6H2z"/></svg>
      +1555 - 628 - 4410
    </li>
    <li>
      <svg viewBox="0 0 18 18" fill="none" stroke="#fff" stroke-width="1.6"><rect x="1" y="3.5" width="16" height="11"/><path d="M1 3.5l8 6.5 8-6.5M1 14.5l6-5.5M17 14.5l-6-5.5"/></svg>
      mvaldane@valdanecompanies.com
    </li>
    <li>
      <svg viewBox="0 0 18 18" fill="none" stroke="#fff" stroke-width="1.3"><circle cx="9" cy="9" r="7.5"/><ellipse cx="9" cy="9" rx="3.2" ry="7.5"/><line x1="1.5" y1="9" x2="16.5" y2="9"/><line x1="2.6" y1="5.5" x2="15.4" y2="5.5"/><line x1="2.6" y1="12.5" x2="15.4" y2="12.5"/></svg>
      www.valdanecompanies.com
    </li>
  </ul>
</section>

<section class="card card--back">
  <div class="regional-mark"><span class="regional-mark__square"></span>Thornmere Regional Center</div>
</section>

</body>
</html>
```